Velmora Sports Foundation website

Velmora sports foundation is a charity organisation that assists young athletes and clubs with the financial assistance they need to progress in their sporting career.

The organisation also establishes mentoring programs to community clubs and individuals.
We envision a home page with a horizontal navigation
Contact Us
Donate: A link to a secure payment system
Meet the team: A list of names and images of the board
Lastly the link to donate should be featured prominently and several times along with cues that lead people to find out more
We prefer limited scrolling and would like to see a clean yet modern design

I am unsure if it needs to be coded or not

Target Market(s)

Potential donors, applications for funds, potential affiliates

Industry/Entity Type

Charity

Coding

Coded - Design and coding required

Number of Pages Required

5+ page

Font styles to use
Sans Serif

Colors
3176b5
ec1f27
34a7d7

Requirements
Must have
• emotionally engaging and informative
• motion enabled pictures
• links to donate
• Music
• Enable video uploads
• Large horizontal pictures of young sports players prominently soccer at this stage
• Social media presence
Nice to have
• Live chat
Should not have
• Images that depict poverty

```html
<!DOCTYPE html>
<html lang="en">
<head>
<meta charset="utf-8">
<title>Velmora Sports Foundation</title>
<link rel="stylesheet" href="https://fonts.googleapis.com/css2?family=Open+Sans:wght@600;700&family=Roboto:wght@400;500;700&display=swap">
<style>
:root{
  --blue:#3176b5;
  --red:#ec1f27;
  --sky:#34a7d7;
  --coral:#e8585c;
  --ink:#333333;
  --muted:#666666;
  --light:#e9e9e9;
  --card:#f4f6f9;
  --line:#dde3ea;
  --white:#ffffff;
  --footer:#e6e6e6;
}
*{box-sizing:border-box;margin:0;padding:0}
html,body{width:1200px;height:2922px;overflow:hidden}
body{position:relative;font-family:"Roboto",Arial,sans-serif;color:var(--ink);background:var(--white)}
.abs{position:absolute}
a{color:inherit;text-decoration:none}

/* header */
.site-header{left:0;top:0;width:1200px;height:113px;background:var(--white)}
.brand{left:86px;top:30px;display:flex;align-items:center;gap:10px}
.brand-dot{width:46px;height:46px;border-radius:50%;background:var(--blue)}
.brand-name{font-family:"Roboto",sans-serif;font-weight:700;font-size:17px;line-height:20px;color:var(--blue);width:120px}
.main-nav{top:46px;font-size:14px;font-weight:500;color:#555;letter-spacing:.3px}
.main-nav a{position:absolute;white-space:nowrap}
.main-nav .active{color:var(--blue)}
.nav-donate{left:997px;top:35px;width:115px;height:43px;border:2px solid var(--red);border-radius:6px;color:var(--blue);font-size:14px;font-weight:500;display:flex;align-items:center;justify-content:center}

/* hero */
.hero{left:0;top:113px;width:1200px;height:526px;background:linear-gradient(180deg,rgba(0,0,0,.1),rgba(0,0,0,.35)),linear-gradient(100deg,#2f5a22 0%,#6f2a26 25%,#b3242b 45%,#3f6d2a 60%,#c8c8c8 78%,#a82a2e 100%)}
.hero-title{left:0;top:292px;width:1200px;text-align:center;font-family:"Open Sans",sans-serif;font-weight:700;font-size:42px;color:var(--white)}
.hero-text{left:330px;top:354px;width:540px;text-align:center;font-size:15px;line-height:21px;color:var(--white)}
.hero-btn{left:540px;top:415px;width:121px;height:37px;border:1px solid var(--white);color:var(--white);font-size:14px;font-weight:500;display:flex;align-items:center;justify-content:center}
.hero-arrow{top:358px;width:38px;height:38px;border-radius:50%;background:rgba(255,255,255,.85)}

/* section headings */
.section-title{left:0;width:1200px;text-align:center;font-family:"Open Sans",sans-serif;font-weight:600;font-size:25px;color:var(--ink)}
.title-rule{left:572px;width:56px;height:3px;background:var(--blue)}

/* program */
.video{left:86px;top:783px;width:500px;height:362px;background:radial-gradient(ellipse at 50% 45%,#3f4a2e 0%,#1c2216 60%,#111 100%)}
.play{left:311px;top:939px;width:52px;height:52px}
.event{left:614px;width:498px;height:107px;background:var(--card);border:1px solid var(--line)}
.event-date{position:absolute;left:0;top:0;width:128px;height:105px;border-right:1px solid var(--line);text-align:center;color:var(--red)}
.event-day{display:block;margin-top:14px;font-size:42px;font-weight:500;line-height:46px}
.event-month{display:block;font-size:19px}
.event-title{position:absolute;left:128px;width:370px;top:22px;text-align:center;font-size:22px;font-weight:500;color:var(--blue)}
.event-meta{position:absolute;left:128px;width:370px;top:62px;text-align:center;font-size:12px;color:var(--muted)}

/* team */
.team-band{left:0;top:1225px;width:1200px;height:483px;background:var(--light)}
.member{top:1373px;width:237px;height:220px;background:var(--white);box-shadow:0 1px 3px rgba(0,0,0,.12)}
.member-photo{width:237px;height:179px}
.member-name{position:absolute;left:0;bottom:0;width:237px;height:41px;background:var(--coral);color:var(--white);font-size:16px;font-weight:700;display:flex;align-items:center;justify-content:center}
.view-more{left:0;top:1636px;width:1200px;text-align:center;font-size:16px;font-weight:500;color:var(--blue)}

/* packages */
.packages{left:0;top:1708px;width:1200px;height:481px;background:linear-gradient(180deg,rgba(20,20,20,.82),rgba(30,30,30,.78)),linear-gradient(90deg,#3a4a30,#2b2b2b 50%,#4a3a34)}
.packages .section-title{color:var(--white);font-weight:700;top:64px}
.plan{top:142px;width:326px;height:265px;border:1px solid rgba(255,255,255,.75);text-align:center;color:var(--white)}
.plan-name{margin-top:34px;font-size:20px;font-weight:700;font-family:"Open Sans",sans-serif}
.plan-price{margin-top:14px;font-size:32px;font-weight:700;color:var(--coral)}
.plan-price small{font-size:15px;color:var(--white);font-weight:500}
.plan-text{margin:14px auto 0;width:240px;font-size:13px;line-height:18px}
.plan-btn{display:inline-flex;margin-top:24px;width:122px;height:34px;background:var(--blue);border-radius:2px;color:var(--white);font-size:12px;font-weight:500;align-items:center;justify-content:center}

/* donate strip */
.donate-strip{left:0;top:2189px;width:1200px;height:131px;background:var(--light)}
.donate-line{left:0;top:26px;width:1200px;text-align:center;font-size:22px;font-weight:500;color:var(--blue)}
.donate-btn{left:540px;top:69px;width:122px;height:35px;background:var(--red);border-radius:2px;color:var(--white);font-size:13px;font-weight:500;display:flex;align-items:center;justify-content:center}

/* testimonials */
.testimonials{left:0;top:2320px;width:1200px;height:323px;background:linear-gradient(180deg,rgba(15,15,15,.8),rgba(25,25,25,.75)),linear-gradient(90deg,#2f3d28,#3a3a3a 55%,#6a3536)}
.testimonials .section-title{color:var(--white);font-weight:700;top:42px}
.quote{left:270px;top:94px;width:660px;text-align:center;font-size:14px;line-height:22px;color:var(--white)}
.avatar{left:469px;top:181px;width:98px;height:98px;border-radius:50%;background:radial-gradient(circle at 50% 40%,#c9927a,#4a2a24);border:4px solid rgba(255,255,255,.25)}
.author{left:584px;top:200px;color:var(--white)}
.author-name{font-family:"Open Sans",sans-serif;font-weight:700;font-size:19px}
.author-role{font-size:13px;margin-top:4px}

/* footer */
.site-footer{left:0;top:2643px;width:1200px;height:230px;background:var(--footer)}
.footer-brand{left:86px;top:44px;display:flex;align-items:center;gap:10px}
.live-chat{left:109px;top:162px;width:109px;height:39px;background:var(--sky);border:3px solid #a9d8ee;color:var(--white);font-size:15px;font-weight:700;display:flex;align-items:center;justify-content:center}
.footer-heading{top:48px;font-family:"Open Sans",sans-serif;font-weight:600;font-size:19px;color:#444}
.contact-row{left:319px;display:flex;gap:18px;font-size:13px;line-height:19px;color:#555;align-items:flex-start}
.contact-row svg{flex:none;margin-top:1px}
.quick-links{left:594px;top:98px;list-style:none;font-size:14px;color:#555;line-height:22px}
.quick-links li{display:flex;align-items:center;gap:10px}
.quick-links li::before{content:"";border-left:6px solid #555;border-top:4px solid transparent;border-bottom:4px solid transparent}
.news-input{left:818px;top:100px;width:224px;height:37px;background:var(--white);border:1px solid #d4d4d4;font-size:11px;color:#999;padding:12px 0 0 10px}
.news-btn{left:1042px;top:100px;width:70px;height:37px;background:var(--blue);color:var(--white);font-size:11px;font-weight:700;display:flex;align-items:center;justify-content:center;border-radius:0 4px 4px 0}
.social{top:161px;width:32px;height:32px;border-radius:50%;border:1px solid #999;background:var(--white)}
.copyright{left:0;top:2873px;width:1200px;height:49px;background:var(--white);text-align:center;font-size:12px;line-height:49px;color:#555}
</style>
</head>
<body>

<header class="site-header abs">
  <div class="brand abs"><span class="brand-dot"></span><span class="brand-name">Velmora Sports Foundation</span></div>
  <nav class="main-nav abs" style="left:0;width:1200px">
    <a class="active" style="left:388px">HOME</a>
    <a style="left:475px">PROGRAM ⌄</a>
    <a style="left:606px">DONATE</a>
    <a style="left:709px">MEET THE TEAM</a>
    <a style="left:863px">CONTACT US</a>
  </nav>
  <a class="nav-donate abs">DONATE NOW</a>
</header>

<section class="hero abs" role="img" aria-label="Young soccer players in red and white kits competing for the ball on a grass pitch"></section>
<h1 class="hero-title abs">VELMORA SPORTS FOUNDATION</h1>
<p class="hero-text abs">Is a charity organisation that assists young athletes and clubs with the financial assistance they need to progress in their sporting career.</p>
<a class="hero-btn abs">READ MORE</a>
<span class="hero-arrow abs" style="left:20px"><svg width="38" height="38" viewBox="0 0 38 38"><path d="M22 11 L14 19 L22 27" fill="none" stroke="#555" stroke-width="3"/></svg></span>
<span class="hero-arrow abs" style="left:1142px"><svg width="38" height="38" viewBox="0 0 38 38"><path d="M16 11 L24 19 L16 27" fill="none" stroke="#555" stroke-width="3"/></svg></span>

<h2 class="section-title abs" style="top:686px">OUR PROGRAM</h2>
<span class="title-rule abs" style="top:729px"></span>

<div class="video abs" role="img" aria-label="Video still of a soccer champions league emblem under stadium lights"></div>
<svg class="play abs" viewBox="0 0 52 52"><circle cx="26" cy="26" r="24" fill="rgba(0,0,0,.35)" stroke="#fff" stroke-width="2"/><path d="M21 16 L37 26 L21 36 Z" fill="#fff"/></svg>

<article class="event abs" style="top:783px"><div class="event-date"><span class="event-day">06</span><span class="event-month">DEC</span></div><div class="event-title">LOREM - VS - YOUNG</div><div class="event-meta">12.00, LOREM IPSUM - YOUNG</div></article>
<article class="event abs" style="top:910px"><div class="event-date"><span class="event-day">27</span><span class="event-month">DEC</span></div><div class="event-title">LOREM - VS - YOUNG</div><div class="event-meta">12.00, LOREM IPSUM - YOUNG</div></article>
<article class="event abs" style="top:1036px"><div class="event-date"><span class="event-day">05</span><span class="event-month">JAN</span></div><div class="event-title">LOREM - VS - YOUNG</div><div class="event-meta">12.00, LOREM IPSUM - YOUNG</div></article>

<section class="team-band abs"></section>
<h2 class="section-title abs" style="top:1276px">MEET THE TEAM</h2>
<span class="title-rule abs" style="top:1319px"></span>

<div class="member abs" style="left:86px"><div class="member-photo" role="img" aria-label="Team member in a blue kit sliding on one knee beside a soccer ball" style="background:linear-gradient(180deg,#fff,#e6eef3)"></div><div class="member-name">TOMAS REYD</div></div>
<div class="member abs" style="left:351px"><div class="member-photo" role="img" aria-label="Team member in a navy shirt holding a rugby ball" style="background:linear-gradient(180deg,#fff,#e7ebf0)"></div><div class="member-name">ARAN COLBY</div></div>
<div class="member abs" style="left:614px"><div class="member-photo" role="img" aria-label="Team member in a red kit holding a soccer ball" style="background:linear-gradient(180deg,#fff,#f3e4e4)"></div><div class="member-name">MIRA LANNE</div></div>
<div class="member abs" style="left:877px"><div class="member-photo" role="img" aria-label="Team member in a red kit holding up a soccer ball" style="background:linear-gradient(180deg,#fff,#f3e4e4)"></div><div class="member-name">DEVIN ORR</div></div>

<a class="view-more abs">VIEW MORE &gt;&gt;</a>

<section class="packages abs" role="img" aria-label="Dimmed background of a soccer match">
  <h2 class="section-title abs">CHOOSE YOUR PACKAGE</h2>
  <div class="plan abs" style="left:88px"><div class="plan-name">JUNIOR</div><div class="plan-price">$379<small>/MO</small></div><p class="plan-text">Lorem Ipsum passages, and more recently with desktop publishing software</p><a class="plan-btn">SUBSCRIBE</a></div>
  <div class="plan abs" style="left:438px"><div class="plan-name">INDIVIDUAL</div><div class="plan-price">$987<small>/MO</small></div><p class="plan-text">Lorem Ipsum passages, and more recently with desktop publishing software</p><a class="plan-btn">SUBSCRIBE</a></div>
  <div class="plan abs" style="left:787px"><div class="plan-name">GROUP</div><div class="plan-price">$500<small>/MO</small></div><p class="plan-text">Lorem Ipsum passages, and more recently with desktop publishing software</p><a class="plan-btn">SUBSCRIBE</a></div>
</section>

<section class="donate-strip abs">
  <p class="donate-line abs">Lorem Ipsum as their default model text, and a search for 'lorem ipsum'</p>
  <a class="donate-btn abs">DONATE NOW</a>
</section>

<section class="testimonials abs" role="img" aria-label="Dimmed background of young soccer players in action">
  <h2 class="section-title abs">OUR TESTIMONIALS</h2>
  <p class="quote abs">There are many variations of passages of Lorem Ipsum available, but the majority have suffered alteration in some form, by injected humourThere are many variations of passages of Lorem Ipsum available, but the majority have suffered alteration in some form, by injected humour</p>
  <div class="avatar abs" role="img" aria-label="Portrait photo of the athlete"></div>
  <div class="author abs"><div class="author-name">Lena Parfitt,</div><div class="author-role">Athlete</div></div>
</section>

<footer class="site-footer abs">
  <div class="footer-brand abs"><span class="brand-dot"></span><span class="brand-name">Velmora Sports Foundation</span></div>
  <a class="live-chat abs">LIVE CHAT</a>

  <h3 class="footer-heading abs" style="left:319px">CONTACT US</h3>
  <div class="contact-row abs" style="top:96px"><svg width="14" height="16" viewBox="0 0 14 16"><path d="M3 1 L6 4 L4.5 6 C5.5 8.5 7 10 9.5 11.5 L11 10 L14 13 L12 15.5 C6 15 1 9.5 0.5 3.5 Z" fill="#555"/></svg><span>555-014-2290</span></div>
  <div class="contact-row abs" style="top:126px"><svg width="14" height="18" viewBox="0 0 14 18"><path d="M7 0 C3 0 0 3 0 7 C0 11 7 18 7 18 C7 18 14 11 14 7 C14 3 11 0 7 0 Z" fill="#555"/><circle cx="7" cy="7" r="2.5" fill="#e6e6e6"/></svg><span>1.10.32 and 1.10.33<br>Bonorum et Malorum</span></div>
  <div class="contact-row abs" style="top:176px"><svg width="16" height="12" viewBox="0 0 16 12"><rect x="0.75" y="0.75" width="14.5" height="10.5" fill="none" stroke="#555" stroke-width="1.5"/><path d="M1 1 L8 7 L15 1" fill="none" stroke="#555" stroke-width="1.5"/></svg><span>info@velmorasports.org</span></div>

  <h3 class="footer-heading abs" style="left:594px">QUICK LINKS</h3>
  <ul class="quick-links abs">
    <li>Home</li><li>Program</li><li>Donate</li><li>Meet the Team</li><li>Contact us</li>
  </ul>

  <h3 class="footer-heading abs" style="left:818px">NEWSLETTER</h3>
  <div class="news-input abs">Enter Your Mail</div>
  <a class="news-btn abs">SUBSCRIBE</a>
  <span class="social abs" style="left:818px" aria-label="Social profile"></span>
  <span class="social abs" style="left:861px" aria-label="Social profile"></span>
  <span class="social abs" style="left:904px" aria-label="Social profile"></span>
  <span class="social abs" style="left:947px" aria-label="News feed"></span>
</footer>

<div class="copyright abs">© Copyright 2016 Velmora sports foundation.All Rights Reserved</div>

</body>
</html>
```